real esate business card with company logo and name

we need a business card design for a real esate company

The company name is Walsh & Brand Pty Ltd, and we have our logo designed and will upload. We want classic or moden feel. Black or white background. looks more textured. Should include folowinginformations
Owen Walsh and Lucy Brand
Sales Agents & Onsite Manager
p: 07 5948 2063
F: 07 5948 2174
M:0431 857 219
3/42 Marlow Crescent, FERNLEA QLD 4213

We want this business card looks professonal. Thank you in advance.

Industry/Entity Type

Real Estate Agent

Contact Information for Business Card

Owen Walsh and Lucy Brand
Onsite Manager & Sales Agents
p: 07 5948 2063
M:0431 857 219

Font styles to use
Serif

Colors
000000
fbfbfb
333333
959595

Requirements
Must have
• company logo and name, black or white back ground

```html
<!DOCTYPE html>
<html lang="en">
<head>
<meta charset="utf-8">
<title>Walsh &amp; Brand Pty Ltd – Business Card</title>
<link rel="stylesheet" href="https://fonts.googleapis.com/css2?family=Tinos:wght@400&family=Montserrat:wght@400&display=swap">
<style>
  :root {
    --black: #000000;
    --ink: #111111;
    --charcoal: #333333;
    --grey: #959595;
    --silver-light: #dcdcdc;
    --silver-dark: #a9a9a9;
    --paper: #fbfbfb;
    --backdrop: #e6e6e6;
  }
  * { margin: 0; padding: 0; box-sizing: border-box; }
  html, body {
    width: 1200px; height: 892px; overflow: hidden;
    background: var(--backdrop);
  }
  .stage {
    width: 1200px; height: 892px;
    display: flex; align-items: center; justify-content: center;
  }
  .card {
    position: relative;
    width: 880px; height: 504px;
    background: linear-gradient(160deg, #1a1a1a 0%, var(--black) 60%, #0b0b0b 100%);
    border-radius: 6px;
    overflow: hidden;
  }
  .card__tab {
    position: absolute;
    right: 0; top: 40px;
    width: 70px; height: 424px;
    border-radius: 18px 0 0 18px;
    background: linear-gradient(180deg, var(--silver-light), var(--silver-dark));
  }
  .card__panel {
    position: absolute;
    left: 0; top: 0; bottom: 0;
    width: 500px;
    border-radius: 0 22px 22px 0;
    background: linear-gradient(200deg, #e4e4e4 0%, #c9c9c9 55%, var(--silver-dark) 100%);
    padding: 46px 40px 0 0;
    text-align: right;
    font-family: "Tinos", "Times New Roman", serif;
  }
  .person__name {
    font-size: 38px; color: var(--charcoal); line-height: 1.05;
  }
  .person__role {
    font-size: 22px; color: var(--paper); line-height: 1.3;
    margin-bottom: 12px;
  }
  .contact {
    margin-top: 22px;
    display: flex; justify-content: flex-end; gap: 18px;
  }
  .contact__lines {
    font-size: 23px; line-height: 1.22; color: var(--paper);
  }
  .contact__icons {
    display: flex; flex-direction: column; gap: 10px; padding-top: 4px;
  }
  .icon {
    width: 18px; height: 18px; background: var(--black);
    display: flex; align-items: center; justify-content: center;
  }
  .brand {
    position: absolute;
    left: 500px; right: 70px; top: 0; bottom: 0;
    display: flex; flex-direction: column; align-items: center; justify-content: center;
    gap: 22px;
  }
  .brand__mark {
    width: 96px; height: 96px; background: var(--silver-light);
  }
  .brand__name {
    font-family: "Montserrat", Arial, sans-serif;
    font-size: 19px; letter-spacing: 1px;
    color: var(--grey); text-transform: uppercase;
  }
</style>
</head>
<body>
<main class="stage">
  <article class="card">
    <div class="card__tab"></div>

    <section class="card__panel">
      <p class="person__name">Owen Walsh</p>
      <p class="person__role">Onsite Manager</p>
      <p class="person__name">Lucy Brand</p>
      <p class="person__role">Sales Agents</p>

      <div class="contact">
        <div class="contact__lines">
          <p>07 5948 2063</p>
          <p>0431 857 219</p>
          <p>3/42 Marlow Crescent,</p>
          <p>FERNLEA QLD 4213</p>
        </div>
        <div class="contact__icons">
          <span class="icon" aria-label="phone">
            <svg width="12" height="12" viewBox="0 0 12 12"><path d="M2.5 1l2 2-1 1.3c.6 1.5 1.7 2.6 3.2 3.2L8 6.5l2 2-1.3 1.8C5 10 2 7 1.7 3.2z" fill="#fbfbfb"/></svg>
          </span>
          <span class="icon" aria-label="mobile">
            <svg width="12" height="12" viewBox="0 0 12 12"><rect x="3" y="1" width="6" height="10" rx="1" fill="none" stroke="#fbfbfb" stroke-width="1.2"/><circle cx="6" cy="9.2" r=".7" fill="#fbfbfb"/></svg>
          </span>
          <span class="icon" aria-label="address">
            <svg width="12" height="12" viewBox="0 0 12 12"><path d="M6 1a3.3 3.3 0 0 1 3.3 3.3C9.3 7 6 11 6 11S2.7 7 2.7 4.3A3.3 3.3 0 0 1 6 1z" fill="#fbfbfb"/><circle cx="6" cy="4.3" r="1.1" fill="#000"/></svg>
          </span>
        </div>
      </div>
    </section>

    <section class="brand">
      <div class="brand__mark"></div>
      <p class="brand__name">Walsh &amp; Brand Pty Ltd.</p>
    </section>
  </article>
</main>
</body>
</html>
```